Brackenford Fluidworks needs a website describing the repair business we are in.

Brackenford Fluidworks is a full hydraulic repair facility. We have 2 shops. We repair and service all hydraulic cylinders, pneumatic cylinders, hydraulic pumps, motors, valves and gearboxes. Our services range from large industrial plants to the individual that owns one piece of equipment. We also offer removal and install of cylinders. Along with free pick up and delivery, within a certain distance which is usually 100 miles from one of our shops.

With over 30 years experience in the hydraulic business, we can repair or replace any job. There is not a job too big or too small, we service them all.

We have customers that send whole pieces of equipment to us to do complete overhauls on all the hydraulics. Ranging from a country club green roller to a 10 ton boom truck.

Target Market(s)

Industrial plants, road builders, dirt work companies, general contractors, owners of industrial equipment (bulldozers, excavators, loaders, scrapers, motor graders, etc.

Industry/Entity Type

Hydraulic

Number of Pages Required

5+ page

Font styles to use
Sans Serif

Colors
ec1f27
ffffff
aaaaaa

Requirements
Must have
• Information about what we offer and pictures of jobs completed.
Nice to have
• Nice stock photos of jobsites and industrial plants.
Should not have
• Any sort of comical characters.

```html
<!DOCTYPE html>
<html lang="en">
<head>
<meta charset="utf-8">
<title>Brackenford Fluidworks — Hydraulic Repair</title>
<link rel="stylesheet" href="https://fonts.googleapis.com/css2?family=Roboto:wght@400;500;700&family=Open+Sans:wght@400;600&display=swap">
<style>
:root{
  --red:#ec1f27;
  --red-dark:#c8161d;
  --white:#ffffff;
  --grey:#aaaaaa;
  --ink:#222222;
  --text:#444444;
  --muted:#666666;
  --line:#dddddd;
  --band-wine:#5a1a1a;
  --soft:#efebe8;
}
*{box-sizing:border-box;margin:0;padding:0}
html,body{width:1200px;height:3371px;overflow:hidden;background:var(--white)}
body{font-family:"Open Sans",Arial,sans-serif;color:var(--text);position:relative}
h1,h2,h3,h4,.heading{font-family:"Roboto",Arial,sans-serif;font-weight:500;color:var(--ink)}
section,header,footer{position:relative;width:1200px}
.abs{position:absolute}
.btn{position:absolute;display:flex;align-items:center;justify-content:center;font-family:"Roboto",Arial,sans-serif;font-weight:500;color:var(--white);background:var(--red);text-decoration:none}

/* header */
.site-header{height:108px;background:var(--white);box-shadow:0 1px 4px rgba(0,0,0,.08);z-index:2}
.brand{left:96px;top:10px;display:flex;flex-direction:column;align-items:center;width:118px}
.brand-dot{width:54px;height:54px;border-radius:50%;background:var(--red)}
.brand-name{margin-top:6px;font-family:"Roboto",Arial,sans-serif;font-weight:700;font-size:13px;color:var(--red);text-align:center;line-height:1.1;letter-spacing:.3px}
.social-top{top:22px;left:838px;display:flex;gap:14px}
.social-top span{width:32px;height:32px;border-radius:50%;border:1px solid var(--line);background:var(--white)}
.social-top span::after{content:"";display:block;width:10px;height:10px;border-radius:50%;background:var(--red);margin:10px auto}
.btn-touch{left:990px;top:22px;width:112px;height:32px;font-size:13px}
.main-nav{top:74px;right:98px;display:flex;gap:24px;font-size:14px;font-family:"Open Sans",Arial,sans-serif;color:#333}
.main-nav .active{color:var(--red)}

/* hero */
.hero{height:427px;background:linear-gradient(180deg,#1a2430 0%,#2c3c52 45%,#16202c 100%);overflow:hidden}
.hero-photo{inset:0;background:radial-gradient(ellipse at 70% 30%,rgba(120,150,190,.45),transparent 60%),radial-gradient(ellipse at 20% 70%,rgba(80,110,150,.35),transparent 55%)}
.hero-frame{left:148px;top:64px;width:910px;height:300px;border:1px solid rgba(255,255,255,.12);background:rgba(10,16,24,.35)}
.hero h1{position:absolute;top:96px;width:100%;text-align:center;color:var(--white);font-size:50px;font-weight:700;letter-spacing:-.3px}
.hero p{position:absolute;top:172px;left:220px;width:760px;text-align:center;color:var(--white);font-family:"Roboto",Arial,sans-serif;font-weight:500;font-size:21px;line-height:36px}
.btn-hero{left:526px;top:270px;width:152px;height:50px;font-size:20px;font-weight:400}
.hero-chevron{left:590px;top:390px}

/* about */
.about{height:472px}
.about h2{position:absolute;left:98px;top:82px;font-size:36px;font-weight:400}
.about-text{left:98px;top:140px;width:470px;font-size:11.5px;line-height:23px;color:#333}
.about-text p+p{margin-top:8px}
.btn-about{left:98px;top:331px;width:120px;height:46px;font-size:15px;font-weight:400}
.about-photo{left:625px;top:85px;width:475px;height:292px;background:linear-gradient(135deg,#3a3632 0%,#6b5a44 40%,#c8a86a 55%,#2b3f6e 70%,#4a4440 100%)}

/* experience band */
.experience{height:353px;background:linear-gradient(90deg,#3e1414 0%,#6b2a24 50%,#3e1414 100%);overflow:hidden}
.experience .shade{inset:0;background:radial-gradient(ellipse at 15% 60%,rgba(0,0,0,.35),transparent 50%),radial-gradient(ellipse at 85% 40%,rgba(0,0,0,.3),transparent 50%)}
.experience h3{position:absolute;top:90px;width:100%;text-align:center;color:var(--white);font-size:28px;font-weight:500}
.experience h2{position:absolute;top:136px;width:100%;text-align:center;color:var(--white);font-size:33px;font-weight:500}
.btn-outline{left:524px;top:206px;width:152px;height:53px;background:transparent;border:1px solid var(--white);font-size:16px;font-weight:400;font-family:"Open Sans",Arial,sans-serif}

/* services */
.services{height:506px}
.services h2{position:absolute;top:94px;width:100%;text-align:center;font-size:34px;font-weight:400}
.service{position:absolute;top:158px;width:240px;display:flex;flex-direction:column;align-items:center}
.service-photo{width:205px;height:205px;border-radius:50%}
.service-name{margin-top:14px;font-family:"Roboto",Arial,sans-serif;font-weight:500;font-size:19px;color:#333}
.service-name.light{font-weight:400;color:#444}
.photo-cyl{background:radial-gradient(circle at 40% 45%,#f2d44a,#b8900e 60%,#5a4a20)}
.photo-pneu{background:radial-gradient(circle at 50% 50%,#e8e6e0,#b5a88a 60%,#6a6050)}
.photo-pump{background:radial-gradient(circle at 50% 50%,#d8dde3,#8a9aab 55%,#4a5666)}
.photo-motor{background:radial-gradient(circle at 55% 50%,#4aa8e8,#1c6cb0 55%,#d8dde2 75%)}
.arrow{top:248px}

/* testimonial */
.testimonial{height:399px;background:linear-gradient(90deg,#f2eeea,#e6ddd4 50%,#f2eeea)}
.testimonial h2{position:absolute;top:78px;width:100%;text-align:center;font-size:34px;font-weight:400}
.avatar{left:227px;top:157px;width:110px;height:110px;border-radius:50%;border:3px solid #555;background:linear-gradient(160deg,#e8d3b5,#a8845a)}
.client-name{left:200px;top:278px;width:164px;text-align:center;font-size:16px;color:#555}
.quote{left:440px;top:178px;width:610px;font-size:14px;line-height:26px;color:#444}
.quote b{font-family:"Roboto",Arial,sans-serif;font-size:24px;color:#333;vertical-align:-4px}
.dots{left:584px;top:290px;display:flex;gap:3px}
.dots span{width:7px;height:7px;border-radius:50%;border:1px solid #555}
.dots span.on{background:#555}

/* contact */
.contact{height:503px}
.contact h2{position:absolute;font-size:34px;font-weight:500}
.addr-row{position:absolute;left:112px;display:flex;align-items:flex-start;gap:20px;font-size:21px;color:#333;line-height:38px}
.addr-icon{width:36px;height:36px;border-radius:50%;border:2px solid var(--red);flex:none;display:flex;align-items:center;justify-content:center}
.field{position:absolute;border:1px solid #888;background:var(--white);font-size:11px;color:#555;padding:6px 10px}
.btn-send{left:690px;top:380px;width:140px;height:46px;font-size:16px;font-weight:400;gap:14px}
.btn-send i{width:30px;height:30px;border-radius:50%;background:var(--white);display:flex;align-items:center;justify-content:center}

/* cta */
.cta{height:249px;background:linear-gradient(90deg,#4a3a3a 0%,#8a2a2c 45%,#ec1f27 100%);overflow:hidden}
.cta h2{position:absolute;left:98px;top:50px;width:620px;color:var(--white);font-size:38px;line-height:48px;font-weight:400}
.cta p{position:absolute;left:98px;top:150px;color:var(--white);font-size:15px}
.btn-try{left:905px;top:94px;width:196px;height:64px;background:transparent;border:2px solid var(--white);border-radius:3px;font-size:21px}

/* footer */
.site-footer{height:354px}
.site-footer h4{position:absolute;top:74px;font-size:16px;font-weight:400;color:#222}
.foot-about{left:98px;top:100px;width:220px;font-size:11.5px;line-height:23px;color:#333}
.sub-input{left:380px;top:104px;width:222px;height:30px;border:1px solid #888;font-size:11px;padding:7px 10px;color:#555}
.btn-sub{left:382px;top:146px;width:86px;height:30px;font-size:12px}
.news{position:absolute;left:690px;display:flex;gap:14px;width:250px}
.news-thumb{width:64px;height:52px;flex:none}
.news-text{font-size:11px;line-height:19px;color:#333}
.news-meta{font-size:11px;color:#555;display:flex;gap:18px;margin-top:4px}
.news-meta em{font-style:normal;color:var(--red)}
.follow{left:1002px;top:103px;display:flex;gap:20px}
.follow span{width:12px;height:12px;border-radius:50%;background:var(--red)}
.foot-line{left:98px;top:306px;width:1004px;height:1px;background:#999}
.copyright{top:322px;width:100%;text-align:center;font-size:11px;color:#333}
</style>
</head>
<body>

<header class="site-header">
  <div class="abs brand">
    <span class="brand-dot"></span>
    <span class="brand-name">BRACKENFORD FLUIDWORKS</span>
  </div>
  <div class="abs social-top" aria-label="Social links"><span></span><span></span><span></span></div>
  <a class="btn btn-touch">Get In Touch</a>
  <nav class="abs main-nav">
    <span class="active">Home</span><span>What we do</span><span>Benefits</span><span>Testimonials</span><span>How it works</span><span>Blog</span><span>Contact</span>
  </nav>
</header>

<section class="hero">
  <div class="abs hero-photo" role="img" aria-label="Industrial plant interior with steel piping and machinery in blue light"></div>
  <div class="abs hero-frame"></div>
  <h1>We are a full hydraulic repair facility</h1>
  <p>Our services range from large industrial plants to the individual that owns one piece of equipment.</p>
  <a class="btn btn-hero">Read More</a>
  <svg class="abs hero-chevron" width="20" height="14" viewBox="0 0 20 14"><path d="M3 3l7 7 7-7" fill="none" stroke="#fff" stroke-width="2"/></svg>
</section>

<section class="about">
  <h2>About Us</h2>
  <div class="abs about-text">
    <p>Lorem Ipsum is simply dummy text of the printing and typesetting industry. Lorem Ipsum has been the industry's standard dummy text ever since the 1500s, when an unknown printer took a galley of type and scrambled it to make a type specimen book. It has survived not only five centuries remaining essentially unchanged.</p>
    <p>It was popularised in the 1960s with the release of Transferline sheets containing Lorem Ipsum passages, and more recently with desktop publishing software like Quillset Layout including versions of Lorem Ipsum.</p>
  </div>
  <a class="btn btn-about">Read More</a>
  <div class="abs about-photo" role="img" aria-label="Completed job: hydraulic pump assembly on a wooden pallet in a truck bed"></div>
</section>

<section class="experience">
  <div class="abs shade" role="img" aria-label="Equipment trailer on a jobsite under a dark red tint"></div>
  <h3>With over 30 years experience</h3>
  <h2>In hydraulic business, we can repair / replace any job</h2>
  <a class="btn btn-outline">View Details</a>
</section>

<section class="services">
  <h2>Repair And Service</h2>
  <svg class="abs arrow" style="left:62px" width="14" height="22" viewBox="0 0 14 22"><path d="M11 3L3 11l8 8" fill="none" stroke="#333" stroke-width="2"/></svg>
  <div class="service" style="left:80px"><div class="service-photo photo-cyl" role="img" aria-label="Yellow hydraulic cylinders"></div><span class="service-name">Hydraulic Cylinders</span></div>
  <div class="service" style="left:347px"><div class="service-photo photo-pneu" role="img" aria-label="Pneumatic cylinders and tubing"></div><span class="service-name">Pneumatic Cylinders</span></div>
  <div class="service" style="left:612px"><div class="service-photo photo-pump" role="img" aria-label="Hydraulic pump station with piping"></div><span class="service-name">Hydraulic Pumps</span></div>
  <div class="service" style="left:878px"><div class="service-photo photo-motor" role="img" aria-label="Blue electric motor"></div><span class="service-name light">Motors</span></div>
  <svg class="abs arrow" style="left:1122px" width="14" height="22" viewBox="0 0 14 22"><path d="M3 3l8 8-8 8" fill="none" stroke="#333" stroke-width="2"/></svg>
</section>

<section class="testimonial" role="img" aria-label="Faint background of hydraulic cylinders on a pallet">
  <h2>Testimonial</h2>
  <div class="abs avatar" role="img" aria-label="Client portrait"></div>
  <div class="abs client-name">Maren Holt</div>
  <p class="abs quote"><b>&ldquo;</b> &nbsp;"Lorem Ipsum is simply dummy text of theing and typesetting industry. Lorem ume has eien the industry's standard." &nbsp;<b>&rdquo;</b></p>
  <div class="abs dots"><span class="on"></span><span></span><span></span><span></span></div>
</section>

<section class="contact">
  <h2 style="left:112px;top:94px">Address</h2>
  <div class="addr-row" style="top:154px">
    <span class="addr-icon"><svg width="16" height="16" viewBox="0 0 24 24"><path d="M6.6 10.8a15 15 0 006.6 6.6l2.2-2.2a1 1 0 011-.25 11.4 11.4 0 003.6.57 1 1 0 011 1V20a1 1 0 01-1 1A17 17 0 013 4a1 1 0 011-1h3.5a1 1 0 011 1 11.4 11.4 0 00.57 3.6 1 1 0 01-.25 1z" fill="#ec1f27"/></svg></span>
    <span>(+1) 555 014 0192</span>
  </div>
  <div class="addr-row" style="top:214px">
    <span class="addr-icon"><svg width="16" height="14" viewBox="0 0 24 20"><rect x="1" y="2" width="22" height="16" rx="2" fill="#ec1f27"/><path d="M2 4l10 7 10-7" fill="none" stroke="#fff" stroke-width="2"/></svg></span>
    <span>sales@brackenfordfluidworks.com</span>
  </div>
  <div class="addr-row" style="top:274px">
    <span class="addr-icon"><svg width="14" height="18" viewBox="0 0 14 20"><path d="M7 0a7 7 0 00-7 7c0 5 7 13 7 13s7-8 7-13a7 7 0 00-7-7z" fill="#ec1f27"/><circle cx="7" cy="7" r="2.5" fill="#fff"/></svg></span>
    <span>Lorem Ipsum Is Simply Dummy,<br>Lorem Ipsum is Simple.</span>
  </div>

  <h2 style="left:688px;top:94px">Contact Us</h2>
  <div class="field" style="left:690px;top:160px;width:195px;height:36px">First Name</div>
  <div class="field" style="left:900px;top:160px;width:195px;height:36px">Last Name</div>
  <div class="field" style="left:690px;top:217px;width:195px;height:36px">Phone No</div>
  <div class="field" style="left:900px;top:217px;width:195px;height:36px">Email</div>
  <div class="field" style="left:690px;top:274px;width:405px;height:88px">Message</div>
  <a class="btn btn-send">Send Now <i><svg width="14" height="10" viewBox="0 0 14 10"><path d="M1 5h11M8 1l4 4-4 4" fill="none" stroke="#ec1f27" stroke-width="2"/></svg></i></a>
</section>

<section class="cta" role="img" aria-label="Industrial refinery silhouette under a red gradient">
  <h2>We do complete overhauls on all the hydraulics</h2>
  <p>Free pick up and delivery, within a certain distance which is usually 100 miles from one of our shop</p>
  <a class="btn btn-try">Try Us Now</a>
</section>

<footer class="site-footer">
  <h4 style="left:98px">About</h4>
  <p class="abs foot-about">Lorem Ipsum is simply dummy text of the printing and typesetting industry. Lorem Ipsum has been the industry's standard dummy text.</p>

  <h4 style="left:380px">Subscribe Newsletter</h4>
  <div class="abs sub-input">Enter Your Email</div>
  <svg class="abs" style="left:578px;top:114px" width="14" height="11" viewBox="0 0 24 20"><rect x="1" y="2" width="22" height="16" rx="2" fill="#ec1f27"/><path d="M2 4l10 7 10-7" fill="none" stroke="#fff" stroke-width="2"/></svg>
  <a class="btn btn-sub">Subscribe</a>

  <h4 style="left:688px">Latest News</h4>
  <div class="news" style="top:102px">
    <div class="news-thumb" role="img" aria-label="Workers at a jobsite" style="background:linear-gradient(135deg,#d8b030,#7a6030)"></div>
    <div><div class="news-text">Lorem Iosum is simply dummy text ipsum</div><div class="news-meta"><span><em>&#9632;</em> 1 Mar, 2018</span><span><em>&#9679;</em> 4</span></div></div>
  </div>
  <div class="news" style="top:190px">
    <div class="news-thumb" role="img" aria-label="Pipework in an industrial plant" style="background:linear-gradient(135deg,#c8ccd0,#6a7078)"></div>
    <div><div class="news-text">Lorem Iosum is simply dummy text ipsum</div><div class="news-meta"><span><em>&#9632;</em> 1 Mar, 2018</span><span><em>&#9679;</em> 4</span></div></div>
  </div>

  <h4 style="left:1002px">Follow Us On</h4>
  <div class="abs follow" aria-label="Social links"><span></span><span></span><span></span></div>

  <div class="abs foot-line"></div>
  <p class="abs copyright">Copyright© 2018 . All Rights Reserved.</p>
</footer>

</body>
</html>
```